New design for existing catalog pages

We want to update and improve our existing design. The existing products on the designs should be adopted. Also the prices, descriptions and article numbers.
It is important that we receive an Indesign file that we can adapt. Also replace the images and adjust texts and prices.

Target Market(s)

Older people with high incomes. More conservative people.

Industry/Entity Type

Münzen und Briefmarkenhandel

Requirements
Must have
• Noble, simple and timeless design that looks high quality.
Nice to have
• The expensive products should be presented accordingly
Should not have
• Don't look cheap. Not too many different and bright colors

```html
<!DOCTYPE html>
<html lang="de">
<head>
<meta charset="utf-8">
<title>Katalog – Top Münz-Raritäten & Helvetische Republik</title>
<link rel="stylesheet" href="https://fonts.googleapis.com/css2?family=Lato:wght@400;700;900&family=Roboto+Condensed:wght@500;700&display=swap">
<style>
  :root{
    --navy:#2e3192;
    --navy-deep:#232777;
    --panel:#e2e2e4;
    --backdrop:#ececec;
    --info:#d9eef9;
    --ink:#222;
    --white:#fff;
    --gold-light:#f4e3a0;
    --gold:#d8b55a;
    --gold-dark:#9a7a2e;
  }
  *{margin:0;padding:0;box-sizing:border-box}
  html,body{width:1200px;height:2487px;overflow:hidden;background:var(--backdrop)}
  body{position:relative;font-family:"Lato",sans-serif;color:var(--ink)}
  .page{position:absolute;left:183px;width:834px;background:var(--white);box-shadow:0 2px 8px rgba(0,0,0,.18)}
  .page--rarities{top:84px;height:1156px}
  .page--republic{top:1270px;height:1157px}
  .page-head{position:absolute;left:38px;width:758px;font-weight:900;font-size:20px;color:var(--navy);border-bottom:2px solid var(--navy);line-height:24px}
  .panel{position:absolute;left:38px;width:758px;background:var(--panel);overflow:hidden}
  .panel-title{position:absolute;left:0;width:100%;text-align:center;font-weight:900;font-size:28px;color:var(--navy);text-decoration:underline;text-decoration-thickness:2px;text-underline-offset:4px;letter-spacing:.2px}
  .copy{position:absolute;font-size:12.2px;line-height:16.5px;color:var(--ink);z-index:2}
  .copy--wrap{line-height:16px}
  .coin-wrap{float:right;width:140px;height:170px;shape-outside:circle(132px at 224px 136px)}
  .coin{position:absolute;border-radius:50%;
    background:radial-gradient(circle at 38% 35%,var(--gold-light) 0%,var(--gold) 55%,var(--gold-dark) 100%);
    box-shadow:2px 4px 8px rgba(0,0,0,.35)}
  .coin--pale{background:radial-gradient(circle at 38% 35%,#fbf1cf 0%,#e8d28e 55%,#b3944a 100%)}
  .coin--yellow{background:radial-gradient(circle at 38% 35%,#fbe678 0%,#e2bd2c 55%,#a57f14 100%)}
  .sweep{position:absolute}
  .specs{position:absolute;background:var(--info);padding:8px}
  .specs ul{list-style:none;border:1px solid #8ea3b5;padding:3px 8px 3px 10px;font-size:11.2px;line-height:15px}
  .specs li{position:relative;padding-left:16px}
  .specs li::before{content:"";position:absolute;left:1px;top:5px;width:5px;height:5px;border-right:1.4px solid #555;border-top:1.4px solid #555;transform:rotate(45deg)}
  .specs--ticks li::before{left:0;top:3px;width:5px;height:9px;border:none;border-right:2px solid var(--navy);border-bottom:2px solid var(--navy);border-top:none;transform:rotate(40deg)}
  .sku,.price{position:absolute;font-family:"Roboto Condensed",sans-serif;font-weight:700;font-size:20px;color:#111}
  .ribbon{position:absolute}
  .ribbon span{position:absolute;left:0;right:0;top:0;bottom:0;display:flex;align-items:center;justify-content:center;font-family:"Roboto Condensed",sans-serif;font-weight:700;color:var(--white);font-size:19px}
  .page-foot{position:absolute;right:44px;font-weight:900;font-size:17px;color:var(--navy)}
  .cols{position:absolute;font-size:13.3px;line-height:18.2px;text-align:justify}
  .cols p{margin-bottom:8px}
  .order-row{position:absolute;left:38px;width:758px;height:30px;font-family:"Roboto Condensed",sans-serif;font-weight:700;font-size:19.5px;color:#111}
  .order-row .sku-cell{position:absolute;left:18px}
  .order-row .name-cell{position:absolute;left:0;right:0;text-align:center}
  .order-row .price-cell{position:absolute;right:18px}
  .foot-band{position:absolute;left:38px;top:1110px;width:758px;height:33px;background:var(--navy);color:var(--white);font-weight:900;font-size:17px;text-align:right;padding-right:12px;line-height:33px}
</style>
</head>
<body>

<section class="page page--rarities">
  <h2 class="page-head" style="top:28px">Top Münz-Raritäten</h2>

  <article class="panel" style="top:57px;height:347px">
    <svg class="sweep" style="left:0;top:0" width="758" height="347" viewBox="0 0 758 347" aria-hidden="true">
      <path d="M408 347 C440 250 620 220 758 150 L758 347 Z" fill="var(--navy)"/>
    </svg>
    <h3 class="panel-title" style="top:8px">20 Franken 1873, 3-Punkt - Probeprägung</h3>
    <div class="coin" role="img" aria-label="Goldmünze 20 Franken 1873, Wertseite mit Eichenkranz" style="left:256px;top:75px;width:246px;height:246px"></div>
    <div class="coin" role="img" aria-label="Goldmünze 20 Franken 1873, Bildseite mit sitzender Helvetia und Wappenschild" style="left:487px;top:66px;width:264px;height:264px"></div>
    <div class="copy copy--wrap" style="left:19px;top:60px;width:276px">
      <div class="coin-wrap" aria-hidden="true"></div>
      1873 liess das Finanzdepartement vom bekannten Graveur Anton Weiler in seiner Prägestätte in Brüssel ein Stempelpaar und 1‘000 Exemplare einer neuen Eidgenössischen Goldmünze anfertigen. Der oberste der drei Punkte beinhaltete das Münzzeichen des Graveurs und stellte einen Engelskopf dar, der jedoch bei oberflächlicher Betrachtung als Punkt wahrgenommen wird.
    </div>
    <div class="specs" style="left:19px;top:208px;width:222px;height:96px">
      <ul>
        <li>Jahr 1873</li>
        <li>Gold – 900/1‘000 Feinheit</li>
        <li>Gewicht 6,451 Gramm</li>
        <li>Durchmesser 21mm</li>
        <li>Auflage: 1‘000 Stück</li>
      </ul>
    </div>
    <div class="sku" style="left:20px;top:313px">7870.1873.01</div>
    <div class="price" style="left:200px;top:313px">9995,– CHF</div>
  </article>

  <article class="panel" style="top:414px;height:345px">
    <svg class="sweep" style="left:0;top:0" width="758" height="345" viewBox="0 0 758 345" aria-hidden="true">
      <path d="M0 150 C120 200 300 240 340 345 L0 345 Z" fill="var(--navy)"/>
    </svg>
    <h3 class="panel-title" style="top:8px">Das 100 Franken Vreneli von 1925</h3>
    <div class="coin coin--pale" role="img" aria-label="Goldmünze 100 Franken 1925, Wertseite mit Strahlenkreuz und Alpenblumen" style="left:12px;top:58px;width:290px;height:290px"></div>
    <div class="coin coin--pale" role="img" aria-label="Goldmünze 100 Franken 1925, Helvetiakopf vor Bergkulisse" style="left:276px;top:58px;width:280px;height:280px"></div>
    <svg class="ribbon" style="left:557px;top:77px" width="180" height="38" viewBox="0 0 180 38" aria-hidden="true">
      <defs><linearGradient id="rib1" x1="0" y1="0" x2="0" y2="1"><stop offset="0" stop-color="#2a6fb0"/><stop offset="1" stop-color="#173e80"/></linearGradient></defs>
      <polygon points="0,8 14,0 14,30 0,38" fill="#10306a"/>
      <polygon points="180,8 166,0 166,30 180,38" fill="#10306a"/>
      <rect x="10" y="3" width="160" height="30" fill="url(#rib1)"/>
    </svg>
    <div class="ribbon" style="left:557px;top:77px;width:180px;height:36px"><span>Top - Rarität</span></div>
    <p class="copy" style="left:562px;top:125px;width:185px;line-height:16.8px">1925, 100 Fr. Gold-Vreneli, bis unzirkuliert, mit Stempelglanz, Top-Erhaltung,<br><span style="display:block;margin-top:4px">Durchmesser: 35mm,</span><span style="display:block;margin-top:4px">Motiv: Helvetiakopf (Vreneli),</span><span style="display:block;margin-top:4px">Entwurf: Félix Ulrich Lambert, Neuchâtel, Münzzeichen B,</span><span style="display:block;margin-top:4px">Auflage: 5‘000</span></p>
    <div class="sku" style="left:564px;top:282px">7874.1925.08</div>
    <div class="price" style="left:564px;top:313px">25900,– CHF</div>
  </article>

  <article class="panel" style="top:770px;height:346px">
    <svg class="sweep" style="left:0;top:0" width="758" height="346" viewBox="0 0 758 346" aria-hidden="true">
      <path d="M413 346 C450 250 640 210 758 155 L758 346 Z" fill="var(--navy)"/>
    </svg>
    <h3 class="panel-title" style="top:8px">Das 100 Franken Vreneli von 1925</h3>
    <svg class="ribbon" style="left:17px;top:78px" width="180" height="38" viewBox="0 0 180 38" aria-hidden="true">
      <defs><linearGradient id="rib2" x1="0" y1="0" x2="0" y2="1"><stop offset="0" stop-color="#2a6fb0"/><stop offset="1" stop-color="#173e80"/></linearGradient></defs>
      <polygon points="0,8 14,0 14,30 0,38" fill="#10306a"/>
      <polygon points="180,8 166,0 166,30 180,38" fill="#10306a"/>
      <rect x="10" y="3" width="160" height="30" fill="url(#rib2)"/>
    </svg>
    <div class="ribbon" style="left:17px;top:78px;width:180px;height:36px"><span>Top - Qualität</span></div>
    <p class="copy" style="left:20px;top:126px;width:180px">1925, 100 Fr. Gold-Vreneli, fast FDC, Top-Erhaltung, Durchmesser:35mm, Motiv: Helvetiakopf (Vreneli), Entwurf: Félix Ulrich Lambert, Neuchâtel, Münzzeichen B, Auflage: 5‘000</p>
    <div class="sku" style="left:20px;top:240px">7874.1925.07</div>
    <div class="price" style="left:20px;top:273px">25900,– CHF</div>
    <div class="coin coin--pale" role="img" aria-label="Goldmünze 100 Franken 1925, Wertseite mit Strahlenkreuz" style="left:204px;top:60px;width:270px;height:270px"></div>
    <div class="coin coin--pale" role="img" aria-label="Goldmünze 100 Franken 1925, Helvetiakopf" style="left:462px;top:60px;width:270px;height:270px"></div>
  </article>

  <div class="page-foot" style="top:1118px">Top Münz-Raritäten</div>
</section>

<section class="page page--republic">
  <h2 class="page-head" style="top:28px">Helvetische Republik - Duplonen</h2>

  <article class="panel" style="top:61px;height:951px">
    <h3 class="panel-title" style="top:20px;font-size:26px;font-family:'Roboto Condensed',sans-serif;font-weight:700;letter-spacing:-.2px">Duplone und Doppelduplone der Helvetischen Republik 1798 - 1803</h3>
    <div class="cols" style="left:21px;top:61px;width:345px;height:250px;overflow:hidden">
      <p>Helvetische Republik ist die offizielle Bezeichnung des schweizerischen Staatswesens, das am 12. April 1798 die alte Eidgenossenschaft ablöste und bis zum 10. März 1803 bestand.</p>
      <p>Frankreich nutzte die bestehende Unzufriedenheit der ländlichen Eliten in den Untertanengebieten der alten Eidgenossenschaft, sowie der aufgeklärten Bürger in den städtischen Orten und förderte gezielt re-volutionäre Bestrebungen. Angefacht oder ausgelöst und zugleich auch abgesichert wurde die Umwälzung durch französische Truppen, die ab Ende Januar in einer Zangenbewegung von der Waadt und vom Jura her in das westliche Mittelland vorstiessen (Franzoseneinfall). In den Kampfhandlungen</p>
    </div>
    <div class="cols" style="left:394px;top:61px;width:345px">
      <p>Anfang März 1798 ging die alte Eidgenossenschaft unter.</p>
      <p>Einige Städte, allen voran Bern, hatten beträchtliche Vermögen in ihren Schatzkammern. Der sogenannte Staatsschatz von Bern wurde von den Französischen Truppen geplündert. Mehrere Kutschen mit Gold und Silber, sowie die Bären aus dem Bärengraben, wurden nach Paris gekarrt.</p>
      <p>Mit der Einführung der Helvetischen Republik ging das Münzwesen von den Kantonen auf den Zentralstaat über und der Franken wurde als Währung festgelegt. In dieser Zeit entstanden die Duplonen (16 Franken) und Doppelduplonen (32 Franken) der Helvetischen Republik.</p>
    </div>

    <div class="coin coin--yellow" role="img" aria-label="Goldmünze 32 Franken 1800 mit Wertangabe im Kranz" style="left:15px;top:431px;width:394px;height:394px"></div>
    <div class="coin coin--yellow" role="img" aria-label="Goldmünze der Helvetischen Republik, stehender Bannerträger mit Fahne" style="left:374px;top:326px;width:350px;height:350px"></div>
    <div class="coin coin--yellow" role="img" aria-label="Goldmünze 16 Franken 1800 mit Wertangabe im Kranz" style="left:501px;top:665px;width:248px;height:248px"></div>

    <svg class="ribbon" style="left:42px;top:380px" width="240" height="80" viewBox="0 0 240 80" aria-hidden="true">
      <polygon points="4,34 236,6 240,40 8,70" fill="var(--navy)" stroke="#fff" stroke-width="2"/>
    </svg>
    <div class="ribbon" style="left:46px;top:392px;width:232px;height:56px;transform:rotate(-7deg)"><span style="font-size:22px;letter-spacing:.5px">TOP - RARITÄT</span></div>

    <svg class="ribbon" style="left:260px;top:742px" width="240" height="80" viewBox="0 0 240 80" aria-hidden="true">
      <polygon points="4,34 236,6 240,40 8,70" fill="var(--navy)" stroke="#fff" stroke-width="2"/>
    </svg>
    <div class="ribbon" style="left:264px;top:754px;width:232px;height:56px;transform:rotate(-7deg)"><span style="font-size:22px;letter-spacing:.5px">DUPLONENPAAR</span></div>

    <div class="specs specs--ticks" style="left:12px;top:838px;width:232px;height:96px">
      <ul style="border-color:#5a6c9a">
        <li>Schweiz - 16 / 32 Franken</li>
        <li>1800, Helvetische Republik</li>
        <li>7,65 Gramm / 15,26 Gramm - Gold</li>
        <li>23 mm / 29 mm Durchmesser</li>
        <li>vorzüglich bis unzirkuliert</li>
      </ul>
    </div>
  </article>

  <div class="order-row" style="top:1035px">
    <span class="sku-cell">7997.1800.015</span>
    <span class="name-cell">Helvetische Republik - Duplone 16 Franken</span>
    <span class="price-cell">9500,– CHF</span>
  </div>
  <div class="order-row" style="top:1071px">
    <span class="sku-cell">7997.1800.025</span>
    <span class="name-cell">Helvetische Republik - Doppelduplone 32 Franken</span>
    <span class="price-cell">28900,– CHF</span>
  </div>

  <div class="foot-band">Helvetische Republik - Duplone</div>
</section>

</body>
</html>
```